Create modern and sleek business card for luxury real estate company

We're a "boutique" real estate office looking for a design that gets across a highly modern luxury brand. Blacks and whites are probably the best colors unless we try a silver foil for the logo. I've attached a version of our current logo here. I'd like to swap out the current font on there with Gotham Light Regular.

I'm looking to have one side of the card have the logo with the space for our agents info on the other side.

Target Market(s)

Young professionals in a "luxury" headspace

Industry/Entity Type

Real estate

Contact Information for Business Card

A place for agent name, cell number, website. The slogan "Simply Rethinking Real Estate".

Font styles to use
Other font styles liked:
• Gotham Regular

Colors

Designer to choose only greyscale colors for use in the design.

Requirements
Must have
• Matte black as the background color. Clean lines and use of contrast. A specific design aspect that will use silver foil.
Nice to have
• Up in the air on integrating a QR code
Should not have
• Any houses or other real estate related design (ex: a clip art house)

```html
<!DOCTYPE html>
<html lang="en">
<head>
<meta charset="utf-8">
<title>Halden Realty — Business Card</title>
<link href="https://fonts.googleapis.com/css2?family=Libre+Baskerville:wght@400;700&family=Lato:wght@400&display=swap" rel="stylesheet">
<style>
  :root {
    --backdrop: #262626;
    --silver-light: #f1f1f1;
    --silver-mid: #cfcfcf;
    --silver-dark: #a9a9a9;
    --ink: #141414;
    --rule: #7a7a7a;
    --matte-black: #0c0c0c;
    --pattern-tone: #1c1c1c;
    --white: #ffffff;
  }
  * { margin: 0; padding: 0; box-sizing: border-box; }
  html, body { width: 1200px; height: 1108px; overflow: hidden; }
  body {
    background: var(--backdrop);
    display: flex;
    align-items: center;
    justify-content: center;
    gap: 60px;
  }
  .card {
    width: 420px;
    height: 700px;
    border-radius: 26px;
    position: relative;
    overflow: hidden;
  }
  /* Front */
  .card-front {
    background: linear-gradient(160deg, var(--silver-light) 0%, var(--silver-mid) 45%, var(--silver-light) 65%, var(--silver-dark) 100%);
    color: var(--ink);
    text-align: center;
    padding: 150px 40px 0;
  }
  .brand {
    display: flex;
    align-items: center;
    justify-content: center;
    gap: 18px;
  }
  .brand-circle {
    width: 72px; height: 72px;
    border: 3px solid var(--ink);
    border-radius: 50%;
    flex: none;
  }
  .brand-name {
    font-family: "Libre Baskerville", serif;
    font-weight: 400;
    font-size: 34px;
    line-height: 1.15;
    letter-spacing: 1px;
    text-align: left;
    color: var(--ink);
  }
  .agent { margin-top: 150px; }
  .agent-name {
    font-family: "Libre Baskerville", serif;
    font-weight: 700;
    font-size: 24px;
    letter-spacing: 1px;
  }
  .agent-title {
    font-family: "Lato", sans-serif;
    font-size: 17px;
    margin-top: 2px;
  }
  .icon-row {
    display: flex;
    align-items: center;
    justify-content: center;
    gap: 8px;
    margin-top: 16px;
  }
  .icon-row .rule { flex: 1; height: 1px; background: var(--rule); }
  .icon {
    width: 26px; height: 26px;
    background: var(--ink);
    border-radius: 4px;
    display: flex; align-items: center; justify-content: center;
  }
  .contact, .address {
    font-family: "Lato", sans-serif;
    font-size: 18px;
    line-height: 1.45;
  }
  .contact { margin-top: 12px; }
  .divider { height: 1px; background: var(--rule); margin: 14px 20px; }
  /* Back */
  .card-back { background: var(--matte-black); }
  .back-pattern {
    position: absolute; inset: 0;
    background: radial-gradient(ellipse at 60% 35%, #2b2b2b 0%, var(--pattern-tone) 45%, var(--matte-black) 100%);
  }
  .back-mark {
    position: absolute;
    left: 50%; top: 535px;
    transform: translateX(-50%);
    display: flex; align-items: center; gap: 10px;
  }
  .back-mark .brand-circle {
    width: 34px; height: 34px;
    border: 2px solid var(--white);
  }
  .back-mark .brand-name {
    color: var(--white);
    font-size: 13px;
    white-space: nowrap;
  }
</style>
</head>
<body>
  <section class="card card-front">
    <div class="brand">
      <span class="brand-circle"></span>
      <span class="brand-name">HALDEN<br>REALTY</span>
    </div>
    <div class="agent">
      <p class="agent-name">MARCUS HALE</p>
      <p class="agent-title">Managing Director</p>
    </div>
    <div class="icon-row">
      <span class="rule"></span>
      <span class="icon">
        <svg width="16" height="16" viewBox="0 0 16 16"><path d="M3 2h3l1 3-2 1.5a8 8 0 0 0 4.5 4.5L11 9l3 1v3c0 .6-.4 1-1 1A12 12 0 0 1 2 3c0-.6.4-1 1-1z" fill="#fff"/></svg>
      </span>
      <span class="icon">
        <svg width="16" height="16" viewBox="0 0 16 16"><rect x="2" y="4" width="12" height="8" fill="none" stroke="#fff" stroke-width="1.4"/><path d="M2 4l6 5 6-5" fill="none" stroke="#fff" stroke-width="1.4"/></svg>
      </span>
      <span class="icon">
        <svg width="16" height="16" viewBox="0 0 16 16"><circle cx="8" cy="8" r="5.5" fill="none" stroke="#fff" stroke-width="1.4"/><ellipse cx="8" cy="8" rx="2.3" ry="5.5" fill="none" stroke="#fff" stroke-width="1.2"/><path d="M2.5 8h11" stroke="#fff" stroke-width="1.2"/></svg>
      </span>
      <span class="rule"></span>
    </div>
    <div class="contact">
      <p>010-555 0142</p>
      <p>hello@haldenrealty.com</p>
      <p>www.haldenrealty.com</p>
    </div>
    <div class="divider"></div>
    <div class="address">
      <p>88, Ashford Lane</p>
      <p>30917, Norland</p>
    </div>
  </section>

  <section class="card card-back">
    <div class="back-pattern" role="img" aria-label="Tone-on-tone spot gloss pattern of repeated brand marks on matte black"></div>
    <div class="back-mark">
      <span class="brand-circle"></span>
      <span class="brand-name">HALDEN REALTY</span>
    </div>
  </section>
</body>
</html>
```